American cannabis tech company business card design

Pavrel.com is seeking a modern, professional, and brand-aligned business card that represents our company and its core values: Mission, Story, Values, and Impact. As an innovative cannabis company, we want a business card that is not only visually appealing but also serves as a representation of who we are and what we stand for.

Project Scope: Design a double-sided business card that integrates our brand identity and core values. Incorporate our key brand elements, ensuring a sleek and contemporary aesthetic. Visually reflect our core values (Mission, Story, Values, Impact) in a way that is engaging yet professional.

Target Market(s)

Vendors, third parties,

Contact Information for Business Card

Contact details (name, title, email, phone, website, etc.)

Font styles to use
Other font styles liked:
• Caslon, Centra

Colors

Designer to choose colors to be used in the design.

Requirements
Must have
• Pavrel.com logo and branding A creative yet clean way to integrate our core values (Mission, Story, Values, Impact) Modern typography and a well-structured layout
Nice to have
• forest green, grey, white, black
Should not have
• references to marijuana, leafs, plants, or related product

```html
<!DOCTYPE html>
<html lang="en">
<head>
<meta charset="utf-8">
<title>Pavrel.com Business Card</title>
<link href="https://fonts.googleapis.com/css2?family=Poppins:wght@400;500;700;800&display=swap" rel="stylesheet">
<style>
  :root {
    --forest: #1c3a1e;
    --ink: #111111;
    --paper: #ffffff;
    --cream: #fbf8f2;
    --stage: #e6e6e3;
    --rule: #1a1a1a;
  }
  * { margin: 0; padding: 0; box-sizing: border-box; }
  html, body { width: 1200px; height: 1200px; overflow: hidden; }
  body {
    background: var(--stage);
    font-family: 'Poppins', sans-serif;
    position: relative;
  }
  .card {
    position: absolute;
    left: 170px;
    width: 860px;
    height: 490px;
    overflow: hidden;
    box-shadow: 0 6px 18px rgba(0,0,0,0.18);
  }
  /* Front */
  .card-front { top: 90px; background: var(--forest); }
  .front-wordmark {
    position: absolute; top: 150px; left: 0; right: 0;
    text-align: center;
    font-weight: 800; font-size: 124px; letter-spacing: 2px;
    color: var(--cream); line-height: 1;
  }
  .front-web {
    position: absolute; top: 372px; left: 0; right: 0;
    text-align: center;
    font-weight: 500; font-size: 20px; letter-spacing: 5px;
    color: var(--cream);
  }
  /* Back */
  .card-back { top: 620px; background: var(--paper); }
  .back-wordmark {
    position: absolute; top: 108px; left: 52px;
    font-weight: 800; font-size: 86px; letter-spacing: 1px;
    color: var(--forest); line-height: 1;
  }
  .divider {
    position: absolute; left: 440px; top: 86px;
    width: 2px; height: 180px; background: var(--rule);
  }
  .contact { position: absolute; left: 478px; top: 96px; color: var(--forest); }
  .contact-name { font-weight: 700; font-size: 30px; line-height: 1.05; letter-spacing: 0.5px; }
  .contact-title { font-weight: 500; font-size: 19px; color: var(--ink); margin-bottom: 18px; }
  .contact-row {
    display: flex; align-items: center; gap: 14px;
    font-size: 22px; font-weight: 500; color: var(--ink); line-height: 1.35;
  }
  .contact-row svg { width: 18px; height: 18px; flex: none; }
  .values-band {
    position: absolute; left: 0; top: 322px;
    width: 640px; height: 48px; background: var(--forest);
    color: var(--paper);
    font-weight: 500; font-size: 22px; letter-spacing: 3.5px;
    display: flex; align-items: center; padding-left: 30px;
    white-space: nowrap;
  }
  .values-rule {
    position: absolute; left: 0; top: 376px;
    width: 640px; height: 3px; background: var(--rule);
  }
  .social { position: absolute; right: 48px; top: 366px; display: flex; gap: 20px; }
  .social span {
    width: 34px; height: 34px; border-radius: 5px; background: var(--forest); display: block;
  }
</style>
</head>
<body>
  <section class="card card-front">
    <div class="front-wordmark">PAVREL</div>
    <div class="front-web">www.PAVREL.com</div>
  </section>

  <section class="card card-back">
    <div class="back-wordmark">PAVREL</div>
    <div class="divider"></div>
    <div class="contact">
      <div class="contact-name">JONAH R. ELLIS</div>
      <div class="contact-title">Director</div>
      <div class="contact-row">
        <svg viewBox="0 0 24 24" aria-hidden="true"><path fill="#1c3a1e" d="M6.6 10.8a15 15 0 0 0 6.6 6.6l2.2-2.2a1 1 0 0 1 1-.25 11.4 11.4 0 0 0 3.6.57 1 1 0 0 1 1 1V20a1 1 0 0 1-1 1A17 17 0 0 1 3 4a1 1 0 0 1 1-1h3.5a1 1 0 0 1 1 1c0 1.25.2 2.45.57 3.6a1 1 0 0 1-.25 1z"/></svg>
        <span>+1 555 -010-4821</span>
      </div>
      <div class="contact-row">
        <svg viewBox="0 0 24 24" aria-hidden="true"><rect x="2" y="5" width="20" height="14" fill="#1c3a1e"/><path d="M2 5l10 8 10-8" fill="none" stroke="#fff" stroke-width="1.6"/></svg>
        <span>team@pavrel.com</span>
      </div>
      <div class="contact-row">
        <svg viewBox="0 0 24 24" aria-hidden="true"><circle cx="12" cy="12" r="10" fill="#1c3a1e"/><g fill="none" stroke="#fff" stroke-width="1.2"><ellipse cx="12" cy="12" rx="4" ry="10"/><path d="M2 12h20M4 7h16M4 17h16"/></g></svg>
        <span>www.PAVREL.com</span>
      </div>
    </div>
    <div class="values-band">Mission | Story | Values and Impact</div>
    <div class="values-rule"></div>
    <div class="social" aria-label="Social profiles">
      <span></span><span></span><span></span>
    </div>
  </section>
</body>
</html>
```